Professional & attention grabbing.

A business card design, front and back. I already have a logo I will attach, but I am open to something new as well.
Things to include:
Name:
Title:
Phone:
Email:
Wanting something that is professional but attention grabbing.
Also we do a lot of work using drones on natural gas pipelines (leading the future)if you want to include any of that. I'm open to ideas.
Target Market(s)
Natural gas transmission industry / greenhouse gas mitigation industry
Industry/Entity Type
Business
Colors
Designer to choose colors to be used in the design.
Look and feel
Each slider illustrates characteristics of the customer's brand and the style your logo design should communicate.

```html
<!DOCTYPE html>
<html lang="en">
<head>
<meta charset="utf-8">
<title>Halvard Field Surveys – Business Card</title>
<link rel="stylesheet" href="https://fonts.googleapis.com/css2?family=Oswald:wght@600&family=Montserrat:wght@400;500&display=swap">
<style>
  :root {
    --backdrop: #e9e7e4;
    --card: #ffffff;
    --ink: #3a3a3c;
    --ink-strong: #111111;
    --accent: #c1272d;
  }
  * { margin: 0; padding: 0; box-sizing: border-box; }
  html, body {
    width: 1200px;
    height: 1135px;
    overflow: hidden;
    background: var(--backdrop);
  }
  .canvas {
    position: relative;
    width: 1200px;
    height: 1135px;
  }
  .card {
    position: absolute;
    background: var(--card);
    box-shadow: 0 6px 18px rgba(0,0,0,0.18);
  }
  .card--front { left: 237px; top: 90px; width: 679px; height: 406px; }
  .card--back {
    left: 235px; top: 625px; width: 680px; height: 407px;
    display: flex; align-items: center; justify-content: center;
  }

  .brand {
    display: flex;
    align-items: center;
    gap: 10px;
  }
  .brand__square { background: var(--accent); flex: none; }
  .brand__name {
    font-family: "Oswald", "Arial Narrow", sans-serif;
    font-weight: 600;
    color: var(--ink);
    text-transform: uppercase;
    letter-spacing: 0.02em;
    line-height: 1;
    white-space: nowrap;
  }
  .card--front .brand {
    position: absolute;
    top: 96px; left: 0; right: 0;
    justify-content: center;
  }
  .card--front .brand__square { width: 26px; height: 26px; }
  .card--front .brand__name { font-size: 26px; }
  .card--back .brand { gap: 14px; }
  .card--back .brand__square { width: 36px; height: 36px; }
  .card--back .brand__name { font-size: 36px; }

  .centered {
    position: absolute;
    left: 0; right: 0;
    text-align: center;
    color: var(--ink-strong);
    line-height: 1;
    white-space: nowrap;
  }
  .person__name {
    top: 212px;
    font-family: "Oswald", "Arial Narrow", sans-serif;
    font-weight: 600;
    font-size: 30px;
  }
  .person__title {
    top: 245px;
    font-family: "Montserrat", Arial, sans-serif;
    font-weight: 500;
    font-size: 12px;
    letter-spacing: 0.04em;
  }
  .contact__phone {
    top: 333px;
    font-family: "Montserrat", Arial, sans-serif;
    font-size: 13px;
  }
  .contact__email {
    top: 360px;
    font-family: "Montserrat", Arial, sans-serif;
    font-size: 14px;
    letter-spacing: 0.02em;
  }
</style>
</head>
<body>
  <main class="canvas">
    <section class="card card--front" aria-label="Card front">
      <div class="brand">
        <span class="brand__square"></span>
        <span class="brand__name">Halvard Field Surveys</span>
      </div>
      <p class="centered person__name">Your Name</p>
      <p class="centered person__title">TITLE</p>
      <p class="centered contact__phone">555 014 2297</p>
      <p class="centered contact__email">info@halvardsurveys.com</p>
    </section>

    <section class="card card--back" aria-label="Card back">
      <div class="brand">
        <span class="brand__square"></span>
        <span class="brand__name">Halvard Field Surveys</span>
      </div>
    </section>
  </main>
</body>
</html>
```